Vantro cards

I am in the auto motive, transportation business I would like a business card that is Something cool, modern edgy, having to do with car culture. I offer towing service for high and exotic cars. I also provide towing for collisions and car accidents. I offer open and enclosed transport nationwide.

Target Market(s)

Car culture people high end auto collectors

Industry/Entity Type

Towing car carrier

Contact Information for Business Card

My company colors black yellow and silver

Font styles to use
Serif

```html
<!DOCTYPE html>
<html lang="en">
<head>
<meta charset="utf-8">
<title>Vantro Transportation – Business Cards</title>
<link href="https://fonts.googleapis.com/css2?family=Montserrat:wght@400;600;800&display=swap" rel="stylesheet">
<style>
  :root {
    --backdrop: #d9d6d1;
    --card-white: #ffffff;
    --ink: #1a1a1a;
    --brand-yellow: #f7d54a;
    --rule-yellow: #f3d76a;
    --silver-light: #f4f4f4;
    --silver-mid: #c9c9c9;
    --silver-dark: #8e8e8e;
  }
  * { margin: 0; padding: 0; box-sizing: border-box; }
  html, body {
    width: 900px; height: 1200px; overflow: hidden;
    background: var(--backdrop);
    font-family: "Montserrat", Arial, sans-serif;
    color: var(--ink);
  }
  .canvas { position: relative; width: 900px; height: 1200px; }
  .card {
    position: absolute; left: 80px; width: 742px; height: 441px;
    border-radius: 36px; overflow: hidden;
    box-shadow: 0 6px 14px rgba(0,0,0,0.35);
  }
  .card--front { top: 131px; background: var(--card-white); }
  .card--back {
    top: 638px;
    background:
      conic-gradient(from 20deg at 50% 45%,
        var(--silver-light), var(--silver-dark) 12%, var(--silver-light) 25%,
        var(--silver-mid) 38%, var(--silver-light) 50%, var(--silver-dark) 62%,
        var(--silver-light) 75%, var(--silver-mid) 88%, var(--silver-light));
  }
  .brand-mark {
    display: flex; align-items: center; gap: 10px;
    font-weight: 800; color: var(--ink); letter-spacing: 1px;
  }
  .brand-mark__square { background: var(--brand-yellow); flex: none; }
  .card--front .brand-mark {
    position: absolute; left: 40px; top: 118px; font-size: 44px;
  }
  .card--front .brand-mark__square { width: 28px; height: 28px; }
  .card--back .brand-mark {
    position: absolute; left: 50%; top: 50%;
    transform: translate(-50%, -50%); font-size: 72px;
  }
  .card--back .brand-mark__square { width: 44px; height: 44px; }
  .person { position: absolute; left: 28px; top: 280px; }
  .person__name { font-size: 26px; font-weight: 600; color: var(--brand-yellow); line-height: 1; }
  .person__role { font-size: 16px; margin-top: 8px; }
  .divider {
    position: absolute; left: 28px; top: 339px; width: 677px; height: 2px;
    background: var(--rule-yellow);
  }
  .contacts { position: absolute; left: 28px; top: 351px; list-style: none; font-size: 16px; }
  .contacts li { display: flex; align-items: center; gap: 12px; height: 21.5px; }
  .contacts svg { width: 13px; height: 13px; fill: var(--ink); }
  .address {
    position: absolute; left: 523px; top: 373px; font-size: 16px; line-height: 21.5px;
    font-style: normal;
  }
</style>
</head>
<body>
<div class="canvas">
  <section class="card card--front">
    <div class="brand-mark"><span class="brand-mark__square"></span>Vantro</div>
    <div class="person">
      <p class="person__name">Dorian Hale</p>
      <p class="person__role">Owner</p>
    </div>
    <div class="divider"></div>
    <ul class="contacts">
      <li><svg viewBox="0 0 16 16"><path d="M2 5c0-2 2-3 6-3s6 1 6 3v1h-3V5H5v1H2zM4 7h8l2 7H2z"/></svg>(555) 204-7719</li>
      <li><svg viewBox="0 0 16 16"><path d="M1 3h14v10H1zM1 3l7 6 7-6" stroke="#fff" stroke-width="1"/></svg>info@vantrotransport.com</li>
      <li><svg viewBox="0 0 16 16"><circle cx="8" cy="8" r="7"/><path d="M3 6h10M3 10h10M8 1c-3 4-3 10 0 14M8 1c3 4 3 10 0 14" stroke="#fff" stroke-width="1" fill="none"/></svg>www.vantrotransport.com</li>
    </ul>
    <address class="address">48 Ridgeline Avenue<br>Harlow, PA 17500</address>
  </section>

  <section class="card card--back">
    <div class="brand-mark"><span class="brand-mark__square"></span>Vantro</div>
  </section>
</div>
</body>
</html>
```